full stationary design for a modern sleek design company

we are a design company that does modern minimalistic interior design works as well as other design services for high end clients.
we need a full stationary design including and not limited to (double sided business card, letter head, envelopes, documents folder...etc) that reflects the modern style design we do.
sleek modern and minimalistic is the requirements.
Updates

please use the latest attached files as there was a slight modification on the logo Added Wednesday, March 1, 2017

minor update on the logo files in JPG and PSD has been updated kindly follow the new attachments. Added Thursday, March 2, 2017

Target Market(s)

modern minimalist clients

Industry/Entity Type

Design Agency

Requirements
Must have
• the logo
Nice to have
• i like the colors in the colored 3D logo attached
Should not have
• too many colors

```html
<!DOCTYPE html>
<html lang="en">
<head>
<meta charset="utf-8">
<title>Norvane Studio — Business Card</title>
<link rel="stylesheet" href="https://fonts.googleapis.com/css2?family=Open+Sans:wght@400;600;700&display=swap">
<style>
  :root {
    --backdrop: #d9d6d1;
    --card: #f3f4f5;
    --ink: #2b2b2d;
    --accent: #e8782a;
  }
  * { margin: 0; padding: 0; box-sizing: border-box; }
  html, body {
    width: 1200px; height: 969px; overflow: hidden;
    background: var(--backdrop);
    font-family: "Open Sans", Arial, sans-serif;
    color: var(--ink);
  }
  .card {
    position: absolute; left: 120px; top: 210px;
    width: 960px; height: 548px;
    background: var(--card);
    border-radius: 6px 70px 40px 6px;
    box-shadow: 0 10px 30px rgba(0,0,0,0.12);
  }
  .brand-block {
    position: absolute; left: 34px; top: 34px;
    width: 240px; height: 480px;
    display: flex; flex-direction: column; align-items: flex-start; justify-content: space-between;
  }
  .brand-square {
    width: 240px; height: 240px;
    background: var(--accent);
  }
  .brand-word {
    font-size: 50px; font-weight: 700; letter-spacing: 1px; line-height: 1;
    text-transform: uppercase; color: var(--ink);
  }
  .info {
    position: absolute; right: 108px; top: 66px;
    text-align: right;
  }
  .studio-name {
    display: flex; align-items: center; justify-content: flex-end; gap: 14px;
    font-size: 46px; font-weight: 700; letter-spacing: 2px; line-height: 1;
    text-transform: uppercase; color: var(--ink);
  }
  .studio-mark { width: 22px; height: 22px; background: var(--accent); }
  .studio-tagline {
    margin-top: 8px;
    font-size: 22px; font-weight: 600; letter-spacing: 7px;
    text-transform: uppercase; color: var(--accent);
  }
  .person-name {
    margin-top: 24px;
    font-size: 30px; font-weight: 600; text-transform: uppercase; color: var(--accent);
  }
  .person-role { font-size: 25px; margin-top: 2px; }
  .address { margin-top: 26px; font-size: 24px; line-height: 1.5; }
  .contact { margin-top: 14px; list-style: none; font-size: 24px; }
  .contact li {
    display: flex; align-items: center; justify-content: flex-end; gap: 14px;
    line-height: 1.55; margin-right: -40px;
  }
  .contact svg { width: 24px; height: 24px; fill: var(--accent); flex: none; }
</style>
</head>
<body>
  <main class="card">
    <div class="brand-block">
      <span class="brand-square"></span>
      <span class="brand-word">Norvane</span>
    </div>
    <div class="info">
      <div class="studio-name">Norvane Studio<span class="studio-mark"></span></div>
      <p class="studio-tagline">By Lucien Marlo</p>
      <p class="person-name">Adrian Vell</p>
      <p class="person-role">CEO&amp;Founder</p>
      <p class="address">4120 Cedar Row<br>Westbrook, Maine 04092</p>
      <ul class="contact">
        <li>(555) 214 7730
          <svg viewBox="0 0 24 24" aria-hidden="true"><path d="M6.6 10.8a15.1 15.1 0 0 0 6.6 6.6l2.2-2.2c.3-.3.7-.4 1-.2 1.1.4 2.3.6 3.6.6.6 0 1 .4 1 1V20c0 .6-.4 1-1 1A17 17 0 0 1 3 4c0-.6.4-1 1-1h3.5c.6 0 1 .4 1 1 0 1.3.2 2.5.6 3.6.1.3 0 .7-.2 1z"/></svg>
        </li>
        <li>(555) 380 6142
          <svg viewBox="0 0 24 24" aria-hidden="true"><path d="M7 1h10a2 2 0 0 1 2 2v18a2 2 0 0 1-2 2H7a2 2 0 0 1-2-2V3a2 2 0 0 1 2-2zm0 3v14h10V4zm5 15.5a1.2 1.2 0 1 0 0 2.4 1.2 1.2 0 0 0 0-2.4z"/></svg>
        </li>
        <li>adrian@norvanestudio.com
          <svg viewBox="0 0 24 24" aria-hidden="true"><path d="M2 5h20v14H2zm2 2v.5l8 5 8-5V7zm0 2.8V17h16V9.8l-8 5z"/></svg>
        </li>
        <li>www.norvanestudio.com
          <svg viewBox="0 0 24 24" aria-hidden="true"><circle cx="12" cy="12" r="10"/><path d="M2 12h20M12 2c3 3 3 17 0 20M12 2c-3 3-3 17 0 20" stroke="#f3f4f5" stroke-width="1.5" fill="none"/></svg>
        </li>
      </ul>
    </div>
  </main>
</body>
</html>
```